Verpackungsdesign für Wellness- und Saunaprodukte
Zielgruppe
BaFinn ist ein junges Start-Up, das sich auf Wellness- und Saunaprodukte spezialisiert hat. Unsere Zielgruppe besteht zu beinahe gleichen Teilen aus männlichen und weiblichen Personen zwischen 30 und 60 Jahren. Unsere Produkte befinden sich eher im mittel- bis höherpreisigen Segment, daher streben wir ein hochwertiges Design für unsere Verpackungen an. Unsere Produktpalette reicht von Mentholkristallen, Saunaaufgüssen, bis hin zu Textilien für den Wellnessbereich und soll dementsprechend Menschen ansprechen, die sich einen gewissen Luxus im Alltag auch gönnen.
Aufgabenstellung
Inspiriert von der skandinavischen Sauna Kultur, möchten wir Momente der Erholung und
Entspannung in den Alltag unserer Kunden bringen. Die Geschichte des Saunierens ist eng mit der skandinavischen Kultur verbunden und skandinavische Stilelemente sind zeitgemäß und sprechen ein breites Publikum an. Das Design muss auf Dosen/Tiegel , Karton Verpackungen und Flaschen verschiedener Größen adaptierbar sein (siehe Bild im Anhang).
40g Tiegel(transparent) Höhe 40mm Durchmesser 60mm (ohne Deckel Silber gebürstet)
100g Tiegel(transparent) Höhe 53mm Durchmesser 71mm (ohne Deckel Silber gebürstet)
200g Tiegel(transparent) Höhe 65mm Durchmesser 90mm (ohne Deckel Silber gebürstet)
Karton Verpackung 124,5x49x49mm
Karton Verpackung 100x100x100mm
Flaschenetikett 134x67mm (Braunglas, schwarzer Deckel)
Es soll ein passendes Keyvisual erstellt werden.
Im Anhang sieht man die Verpackungen, Dosen, Flaschen sowie unsere ersten Design Entwürfe (an diese Anordnung der Elemente kann sich der Designer orientieren ). Das Logo bleibt wie gegeben. Das Produkt für die Tiegel soll Mentholkristalle sein.

```html
<!DOCTYPE html>
<html lang="de">
<head>
<meta charset="utf-8">
<title>BaFinn – Etiketten und Verpackung</title>
<link rel="stylesheet" href="https://fonts.googleapis.com/css2?family=Cormorant+SC:wght@500;600&family=Roboto+Condensed:wght@400&family=Montserrat:wght@300;400&display=swap">
<style>
  :root {
    --page: #ffffff;
    --paper: #f7f7f7;
    --paper-jar: #f2f2f2;
    --band-grey: #d6d8d5;
    --band-mint: #d4e0dc;
    --band-rose: #f2d7d8;
    --pine: #3d7563;
    --berry: #c0645f;
    --ink: #222222;
    --emblem: #d9dbd9;
    --rule: #b9bbb9;
    --serif: "Cormorant SC", "Cormorant Garamond", serif;
    --sans: "Roboto Condensed", "Arial Narrow", sans-serif;
    --brand: "Montserrat", Arial, sans-serif;
  }
  * { box-sizing: border-box; margin: 0; padding: 0; }
  html, body { width: 713px; height: 1200px; overflow: hidden; background: var(--page); }
  .canvas { position: relative; width: 713px; height: 1200px; }

  .label { position: absolute; background: var(--paper); overflow: hidden; color: var(--ink); }
  .label > * { position: absolute; }
  .band { left: 0; width: 100%; }
  .band--grey { background: var(--band-grey); }
  .band--mint { background: var(--band-mint); }
  .band--rose { background: var(--band-rose); }

  .brand-tile { background: var(--pine); display: flex; align-items: flex-end; justify-content: center; }
  .brand-tile--berry { background: var(--berry); }
  .brand-name { font-family: var(--brand); font-weight: 300; color: #e4e8e6; line-height: 1; }

  .tag { background: var(--pine); color: #fff; font-family: var(--serif); font-weight: 600;
         display: flex; align-items: center; justify-content: center; text-align: center; line-height: 1.05; letter-spacing: .04em; }
  .tag--berry { background: var(--berry); }

  .emblem { border-radius: 50%; background: var(--emblem); transform: translate(-50%, -50%); }

  .centered { transform: translateX(-50%); text-align: center; white-space: nowrap; }
  .title { font-family: var(--serif); font-weight: 500; letter-spacing: .06em; line-height: 1; }
  .heading { font-family: var(--serif); font-weight: 600; letter-spacing: .12em; line-height: 1; }
  .variant { font-family: var(--serif); font-weight: 600; letter-spacing: .14em; line-height: 1; }
  .subtitle { font-family: var(--sans); line-height: 1; }
  .rule { height: 1px; background: linear-gradient(90deg, transparent, var(--rule) 20%, var(--rule) 80%, transparent); transform: translateX(-50%); }
  .copy { font-family: var(--sans); text-align: center; line-height: 1.4; transform: translateX(-50%); white-space: normal; }
  .amount { font-family: var(--brand); font-weight: 400; line-height: 1; }
</style>
</head>
<body>
<main class="canvas">

  <!-- Flaschenetikett -->
  <section class="label label--bottle" style="left:167px; top:201px; width:359px; height:180px;">
    <div class="band band--grey" style="top:0; height:12px;"></div>
    <div class="band band--mint" style="top:160px; height:20px;"></div>
    <div class="brand-tile" style="left:153px; top:0; width:53px; height:42px; padding-bottom:6px;">
      <span class="brand-name" style="font-size:8px;">BaFinn</span>
    </div>
    <div class="emblem" role="img" aria-label="Blütenornament im Kreis" style="left:180px; top:75px; width:34px; height:34px;"></div>
    <h1 class="title centered" style="left:180px; top:101px; font-size:17px;">Nordische<br>Fichte</h1>
    <div class="rule" style="left:180px; top:140px; width:44px;"></div>
    <p class="variant centered" style="left:180px; top:146px; font-size:7px;">Aufguss</p>
    <div class="tag" style="left:153px; top:160px; width:53px; height:20px; font-size:5.2px;">FÜR DIE SAUNA</div>

    <h2 class="heading centered" style="left:61px; top:31px; font-size:7.5px;">Inhaltsstoffe</h2>
    <p class="copy" style="left:61px; top:51px; width:86px; font-size:4.1px;">Lorem ipsum dolor sit amet, consectetuer adipiscing elit, sed diam nonummy nibh euismod tincidunt ut laoreet dolore magna aliquam erat volutpat. Ut wisi enim ad</p>
    <p class="copy" style="left:61px; top:82px; width:86px; font-size:4.1px;">Lorem ipsum dolor sit amet, consectetuer adipiscing elit, sed diam nonummy nibh euismod</p>
    <p class="copy" style="left:61px; top:103px; width:86px; font-size:4.1px;">Lorem ipsum dolor sit amet, consectetuer adipiscing elit, sed diam nonummy nibh euismod tincidunt ut laoreet dolore magna aliquam erat volutpat. Ut wisi enim ad</p>
    <p class="amount centered" style="left:61px; top:138px; font-size:9px;">250 ml</p>

    <h2 class="heading centered" style="left:299px; top:31px; font-size:7.5px;">Anwendung</h2>
    <p class="copy" style="left:299px; top:51px; width:86px; font-size:4.1px;">Lorem ipsum dolor sit amet, consectetuer adipiscing elit, sed diam nonummy nibh euismod tincidunt ut laoreet dolore magna aliquam erat volutpat. Ut wisi enim ad</p>
    <p class="copy" style="left:299px; top:82px; width:86px; font-size:4.1px;">Lorem ipsum dolor sit amet, consectetuer adipiscing elit, sed diam nonummy nibh euismod</p>
    <p class="copy" style="left:299px; top:103px; width:86px; font-size:4.1px;">Lorem ipsum dolor sit amet, consectetuer adipiscing elit, sed diam nonummy nibh euismod tincidunt ut laoreet dolore magna aliquam erat volutpat. Ut wisi enim ad</p>
    <p class="copy" style="left:299px; top:131px; width:86px; font-size:4.1px;">Lorem ipsum dolor sit amet, consectetuer adipiscing elit, sed diam nonummy nibh euismod tincidunt ut laoreet dolore magna aliquam erat volutpat. Ut wisi enim ad</p>
  </section>

  <!-- Kartonverpackung, Vorderseite -->
  <section class="label label--carton" style="left:303px; top:529px; width:92px; height:256px;">
    <div class="band band--grey" style="top:0; height:16px;"></div>
    <div class="band band--grey" style="top:231px; height:25px;"></div>
    <div class="brand-tile" style="left:20px; top:0; width:49px; height:49px; padding-bottom:10px;">
      <span class="brand-name" style="font-size:8px;">BaFinn</span>
    </div>
    <div class="emblem" role="img" aria-label="Blütenornament im Kreis" style="left:46px; top:94px; width:38px; height:38px;"></div>
    <h1 class="title centered" style="left:46px; top:136px; font-size:11.5px;">Nordische<br>Fichte</h1>
    <div class="rule" style="left:46px; top:166px; width:36px;"></div>
    <p class="variant centered" style="left:46px; top:177px; font-size:6px;">Aufguss</p>
    <div class="tag" style="left:22px; top:231px; width:49px; height:25px; font-size:5px;">FÜR<br>DIE SAUNA</div>
  </section>

  <!-- Tiegeletikett Mentholkristalle -->
  <section class="label label--jar" style="left:86px; top:898px; width:249px; height:86px; background:var(--paper-jar);">
    <div class="band band--grey" style="top:0; height:8px;"></div>
    <div class="band band--grey" style="top:74px; height:12px;"></div>
    <div class="brand-tile" style="left:112px; top:0; width:32px; height:25px; padding-bottom:4px;">
      <span class="brand-name" style="font-size:5px;">BaFinn</span>
    </div>
    <div class="emblem" role="img" aria-label="Blütenornament im Kreis" style="left:128px; top:39px; width:16px; height:16px;"></div>
    <h1 class="title centered" style="left:128px; top:51px; font-size:7.5px;">Menthol<br>Kristalle</h1>
    <div class="rule" style="left:128px; top:68px; width:20px;"></div>
    <div class="tag" style="left:104px; top:74px; width:48px; height:12px; font-size:4px;">FÜR DIE SAUNA</div>

    <h2 class="heading centered" style="left:44px; top:17px; font-size:4.5px;">Inhaltsstoffe</h2>
    <p class="copy" style="left:44px; top:27px; width:56px; font-size:3px;">Lorem ipsum dolor sit amet, consectetuer adipiscing elit, sed diam nonummy nibh euismod tincidunt ut laoreet dolore magna aliquam erat volutpat. Ut wisi enim ad</p>
    <p class="amount centered" style="left:44px; top:58px; font-size:7px;">40 g</p>
    <h2 class="heading centered" style="left:207px; top:17px; font-size:4.5px;">Anwendung</h2>
    <p class="copy" style="left:207px; top:27px; width:56px; font-size:3px;">Lorem ipsum dolor sit amet, consectetuer adipiscing elit, sed diam nonummy nibh euismod tincidunt ut laoreet dolore magna aliquam erat volutpat. Ut wisi enim ad</p>
    <p class="copy" style="left:207px; top:53px; width:56px; font-size:3px;">Lorem ipsum dolor sit amet, consectetuer adipiscing elit, sed diam nonummy nibh</p>
  </section>

  <!-- Tiegeletikett Granatapfel -->
  <section class="label label--jar" style="left:377px; top:898px; width:249px; height:86px; background:var(--paper-jar);">
    <div class="band band--rose" style="top:0; height:8px;"></div>
    <div class="band band--rose" style="top:74px; height:12px;"></div>
    <div class="brand-tile brand-tile--berry" style="left:112px; top:0; width:32px; height:25px; padding-bottom:4px;">
      <span class="brand-name" style="font-size:5px;">BaFinn</span>
    </div>
    <div class="emblem" role="img" aria-label="Blütenornament im Kreis" style="left:128px; top:39px; width:16px; height:16px;"></div>
    <h1 class="title centered" style="left:128px; top:52px; font-size:7.5px;">Granatapfel</h1>
    <p class="subtitle centered" style="left:128px; top:61px; font-size:4.5px;">Meersalzpeeling</p>
    <div class="rule" style="left:128px; top:69px; width:20px;"></div>
    <div class="tag tag--berry" style="left:104px; top:74px; width:48px; height:12px; font-size:4px;">FÜR DEN KÖRPER</div>

    <h2 class="heading centered" style="left:44px; top:17px; font-size:4.5px;">Inhaltsstoffe</h2>
    <p class="copy" style="left:44px; top:27px; width:56px; font-size:3px;">Lorem ipsum dolor sit amet, consectetuer adipiscing elit, sed diam nonummy nibh euismod tincidunt ut laoreet dolore magna aliquam erat volutpat. Ut wisi enim ad</p>
    <p class="amount centered" style="left:44px; top:58px; font-size:7px;">40 g</p>
    <h2 class="heading centered" style="left:207px; top:17px; font-size:4.5px;">Anwendung</h2>
    <p class="copy" style="left:207px; top:27px; width:56px; font-size:3px;">Lorem ipsum dolor sit amet, consectetuer adipiscing elit, sed diam nonummy nibh euismod tincidunt ut laoreet dolore magna aliquam erat volutpat. Ut wisi enim ad</p>
    <p class="copy" style="left:207px; top:53px; width:56px; font-size:3px;">Lorem ipsum dolor sit amet, consectetuer adipiscing elit, sed diam nonummy nibh</p>
  </section>

</main>
</body>
</html>
```